Design required for boutique fire engineering firm in New Zealand

Our website was published based on free Wordpress templates, we'd like something a bit more bespoke, clean and simple.
Updates

Reason: didn't check this finished on a Sunday :)

Target Market(s)

architects, building owners, property developers

Industry/Entity Type

Boutique

Contact Information for Business Card

Logo
Fire Engineering

Marcus Brenley
Principal
+64 21 738 512
marcus@veltrix.nz
veltrix.nz

Number of Pages Required

3 page

Font styles to use
Sans Serif

Requirements
Nice to have
• On the business card, an embossed logo would be great - not sure if that's a design thing or just a print thing?
• Website, existing @ http://veltrix.nz for extent of content and general arrangement that I'm happy with.
• Ability to update the content with project bio's and some photos at a later date would be nice.

```html
<!DOCTYPE html>
<html lang="en">
<head>
<meta charset="utf-8">
<title>Veltrix — Fire Engineering &amp; Training</title>
<link href="https://fonts.googleapis.com/css2?family=Mulish:wght@400;600;700;800&display=swap" rel="stylesheet">
<style>
  :root{
    --brand:#1d5a8a;
    --brand-bright:#2f74bd;
    --button:#2f79c3;
    --about-disc:#0f5688;
    --about-ring:#1b6aa0;
    --heading-blue:#2c6cad;
    --text-dark:#2b2b2b;
    --text-muted:#8a8a8a;
    --footer-bg:#e8e8e9;
    --footer-bar:#d5d5d6;
    --footer-heading:#1a568c;
    --footer-link:#555;
    --white:#fff;
  }
  *{box-sizing:border-box;margin:0;padding:0}
  html,body{width:1200px;height:2476px;overflow:hidden}
  body{font-family:"Mulish",Arial,sans-serif;background:var(--white);position:relative;color:var(--text-dark)}
  .abs{position:absolute}

  /* header */
  .site-header{left:0;top:0;width:1200px;height:108px;background:var(--white)}
  .brand{left:124px;top:24px;display:flex;align-items:center;gap:14px}
  .brand-dot{width:60px;height:60px;border-radius:50%;background:var(--brand)}
  .brand-name{font-weight:800;font-size:46px;color:var(--brand);letter-spacing:0.5px;line-height:1}
  .main-nav{left:504px;top:54px;display:flex;align-items:center;font-size:16px;font-weight:600;letter-spacing:.3px}
  .main-nav a{color:#222;text-decoration:none;padding:0 15px;border-left:1px solid #bbb;line-height:18px}
  .main-nav a:first-child{border-left:none;padding-left:0;color:var(--brand-bright)}
  .nav-flame{left:512px;top:12px}

  /* hero */
  .hero{left:0;top:108px;width:1200px;height:569px;background:linear-gradient(100deg,#6f7f8a 0%,#c9cdd3 30%,#b8463a 42%,#d8d9dc 60%,#e6e6ea 100%)}
  .hero-title{left:0;top:205px;width:1200px;text-align:center;color:var(--white);font-weight:800;font-size:46px;line-height:48px;text-transform:uppercase;letter-spacing:.5px}
  .btn{display:flex;align-items:center;justify-content:center;text-transform:uppercase;font-weight:700;color:var(--white);text-decoration:none}
  .btn-solid{background:var(--button)}
  .hero-btn{left:510px;top:317px;width:178px;height:46px;font-size:17px}
  .hero-dots{left:556px;top:528px;display:flex;gap:8px}
  .hero-dots span{width:15px;height:15px;border-radius:50%;background:var(--white)}
  .hero-dots span:first-child{background:transparent;border:2px solid var(--white)}

  /* about */
  .about{left:0;top:677px;width:1200px;height:473px;background:linear-gradient(90deg,#f0a33a 0%,#c9652c 18%,#7a5a4c 40%,#5a5d63 65%,#3f434a 100%)}
  .about-disc{left:93px;top:30px;width:416px;height:416px;border-radius:50%;background:var(--about-ring);display:flex;align-items:center;justify-content:center}
  .about-disc-inner{width:370px;height:370px;border-radius:50%;background:var(--about-disc);color:var(--white);text-align:center;padding:80px 40px 0}
  .about-title{font-size:30px;font-weight:700;margin-bottom:12px}
  .about-text{font-size:14px;line-height:21px;margin-bottom:14px}
  .btn-outline{border:2px solid var(--white);background:transparent}
  .about-btn{width:136px;height:38px;margin:20px auto 0;font-size:13px}

  /* services */
  .services{left:0;top:1150px;width:1200px;height:515px;background:var(--white)}
  .section-badge{left:562px;top:-24px;width:76px;height:76px;border-radius:50%;background:var(--white);display:flex;align-items:center;justify-content:center}
  .services-title{left:0;top:60px;width:1200px;text-align:center;font-size:30px;font-weight:700;color:var(--heading-blue)}
  .service-card{top:118px;width:298px;height:326px;border:1px solid #cfcfcf;background:var(--white)}
  .service-photo{width:100%;height:174px}
  .service-name{margin-top:18px;text-align:center;font-size:23px;font-weight:600;color:#333}
  .service-text{margin:10px auto 0;width:240px;text-align:center;font-size:12.5px;line-height:18px;color:var(--text-muted)}
  .service-btn{left:86px;top:302px;width:120px;height:34px;font-size:13px}

  /* why */
  .why{left:0;top:1665px;width:1200px;height:450px;background:linear-gradient(160deg,#3a78c0 0%,#2d6bb5 40%,#2a64a8 70%,#3a76bd 100%)}
  .why-flame{left:570px;top:44px}
  .why-title{left:0;top:122px;width:1200px;text-align:center;font-size:32px;font-weight:700;color:var(--white)}
  .why-text{left:230px;top:176px;width:740px;text-align:center;font-size:17px;line-height:22px;color:var(--white)}
  .why-text p+p{margin-top:14px}
  .why-btn{left:516px;top:323px;width:166px;height:48px;font-size:15px}

  /* footer */
  .site-footer{left:0;top:2115px;width:1200px;height:297px;background:var(--footer-bg)}
  .footer-col{top:72px}
  .footer-col h3{font-size:19px;font-weight:600;color:var(--footer-heading);margin-bottom:10px;text-transform:uppercase}
  .footer-col li{list-style:none;font-size:14.5px;color:var(--footer-link);line-height:30px}
  .social{display:flex;gap:8px;margin-top:12px}
  .social span{width:33px;height:33px;border-radius:50%}
  .footer-brand{left:790px;top:70px;display:flex;flex-direction:column;align-items:center;width:280px}
  .footer-brand .brand-dot{width:80px;height:80px;margin-bottom:8px}
  .footer-brand .brand-name{font-size:62px}
  .footer-bar{left:0;top:2412px;width:1200px;height:64px;background:var(--footer-bar);text-align:center;font-size:12.5px;color:#555;line-height:64px}
</style>
</head>
<body>

<header class="site-header abs">
  <div class="brand abs"><span class="brand-dot"></span><span class="brand-name">veltrix</span></div>
  <svg class="nav-flame abs" width="34" height="40" viewBox="0 0 34 40" aria-hidden="true"><path d="M17 2C21 10 30 16 30 26a13 13 0 0 1-26 0c0-6 4-10 7-13 0 5 2 8 5 9-2-7 1-14 1-20z" fill="var(--brand-bright)"/></svg>
  <nav class="main-nav abs">
    <a href="#">HOME</a><a href="#">ABOUT US</a><a href="#">SERVICES</a><a href="#">WHY US</a><a href="#">NEWS</a><a href="#">CONTACT US</a>
  </nav>
</header>

<section class="hero abs" role="img" aria-label="Photo of a smiling safety worker in a hard hat and hi-vis vest holding a fire extinguisher beside a hose reel cabinet">
  <h1 class="hero-title abs">We provide fire engineering<br>&amp; training services</h1>
  <a class="btn btn-solid hero-btn abs" href="#">Read More</a>
  <div class="hero-dots abs"><span></span><span></span><span></span><span></span></div>
</section>

<section class="about abs" role="img" aria-label="Photo of a gloved hand operating a red fire extinguisher in front of flames">
  <div class="about-disc abs">
    <div class="about-disc-inner">
      <h2 class="about-title">About Veltrix</h2>
      <p class="about-text">Praesent elementum elit at tellus nec ultricies sit amet porttitor mattis enim In massa</p>
      <p class="about-text">sed nulla In ullamcorper est eget tempor cursus neque mi consectetuer mi a ultricies massa est sed nisi Class aptent taciti sociosqu ad</p>
      <a class="btn btn-outline about-btn" href="#">Read More</a>
    </div>
  </div>
</section>

<section class="services abs">
  <div class="section-badge abs">
    <svg width="34" height="40" viewBox="0 0 34 40" aria-hidden="true"><path d="M17 2C21 10 30 16 30 26a13 13 0 0 1-26 0c0-6 4-10 7-13 0 5 2 8 5 9-2-7 1-14 1-20z" fill="var(--brand-bright)"/></svg>
  </div>
  <h2 class="services-title abs">What We Do</h2>

  <article class="service-card abs" style="left:127px">
    <div class="service-photo" role="img" aria-label="Photo of an engineer in a hard hat checking a red fire alarm control panel" style="background:linear-gradient(90deg,#e7d6c8,#c9452f 55%,#d9d3cf)"></div>
    <h3 class="service-name">Fire Engineering</h3>
    <p class="service-text">Aortor at ipsum cligula augue bibendum accumsan vestibulum ut commodo dapibus malesuada fringilla eu dapibus</p>
    <a class="btn btn-solid service-btn abs" href="#">Read More</a>
  </article>

  <article class="service-card abs" style="left:453px">
    <div class="service-photo" role="img" aria-label="Photo of a trainee in protective gear using an extinguisher on flames" style="background:linear-gradient(160deg,#7a3a1c,#e0781f 45%,#f2a23a 70%,#8a3518)"></div>
    <h3 class="service-name">Our Training</h3>
    <p class="service-text">Aortor at ipsum cligula augue bibendum accumsan vestibulum ut commodo dapibus malesuada fringilla eu dapibus</p>
    <a class="btn btn-solid service-btn abs" href="#">Read More</a>
  </article>

  <article class="service-card abs" style="left:779px">
    <div class="service-photo" role="img" aria-label="Photo of an inspector with a clipboard checking a row of fire extinguishers" style="background:linear-gradient(90deg,#dfe3ea,#c43a2c 55%,#e6e2e2)"></div>
    <h3 class="service-name">Fire Consulting</h3>
    <p class="service-text">Aortor at ipsum cligula augue bibendum accumsan vestibulum ut commodo dapibus malesuada fringilla eu dapibus</p>
    <a class="btn btn-solid service-btn abs" href="#">Read More</a>
  </article>
</section>

<section class="why abs" role="img" aria-label="Blue-tinted photo of an industrial plant with smoke rising">
  <svg class="why-flame abs" width="60" height="70" viewBox="0 0 34 40" aria-hidden="true"><path d="M17 2C21 10 30 16 30 26a13 13 0 0 1-26 0c0-6 4-10 7-13 0 5 2 8 5 9-2-7 1-14 1-20z" fill="var(--white)"/></svg>
  <h2 class="why-title abs">Why We Are</h2>
  <div class="why-text abs">
    <p>Vivamus porttitor purus nisi eleifend libero a tempus libero lectus feugiat felis Morbi diam mauris viverra in gravida eu mattis in ante Morbi eget arcu Morbi porta</p>
    <p>nonummy nibh ligula pulvinar metus eget consectetuer augue nisi quis lacus Ut ac mi quis lacus mollis aliquam Curabitur iaculis tempus eros Curabitur vel mi sit amet magna malesuada ultrices Ut nisi erat fermentum vel congue id euismod in elit Fusce ultricies orci</p>
  </div>
  <a class="btn btn-outline why-btn abs" href="#">Read More</a>
</section>

<footer class="site-footer abs">
  <div class="footer-col abs" style="left:126px">
    <h3>Company</h3>
    <ul><li>Home</li><li>About Us</li><li>What We Do</li><li>Why Us</li></ul>
  </div>
  <div class="footer-col abs" style="left:340px;top:68px">
    <h3>Resources</h3>
    <ul><li>Fire Engineering</li><li>Fire Consulting</li><li>Our Traning</li><li>Contact Us</li></ul>
  </div>
  <div class="footer-col abs" style="left:559px;top:64px">
    <h3>Contact Info</h3>
    <ul><li>Marcus Brenley</li><li>Principal, Fire Engineer</li><li>021 738 512</li></ul>
    <div class="social">
      <span style="background:#3b5c9c"></span><span style="background:#3fa7e0"></span><span style="background:#d8473a"></span><span style="background:#1a7bb5"></span>
    </div>
  </div>
  <div class="footer-brand abs"><span class="brand-dot"></span><span class="brand-name">veltrix</span></div>
</footer>

<div class="footer-bar abs">© 2017 Company Name&nbsp; All right reserved</div>

</body>
</html>
```